Nanny Share Ecommerce Website for Finding Childcare and Parents who need Childcare BrightPramHub.net

Our company needs an ecommerce website (BrightPramHub.net) for a US subscription based service strictly for nanny sharing that connects families and caregivers. The website would allow families to connect with one another as well as to search for nannies. The service would be searchable for other families by location (by radius or zip code), children demographic (age range/gender/special needs), days of week or times, after school care, school closure days (holidays), etc. The service would also be searchable for nannies based on gender, provider age range, years experience, language, hourly rate, transportation available, certification (CPR first aid), education etc. The search fields would be searchable and sortable and allow to connect with the provider (after paying subscription fee). The service would be similar to tendlyfolk.net in that it would allow for families and caregivers to post photos as well as a short bio of the themselves. There would also be a feedback/star rating mechanism to rate caregivers who have performed work for families (viewable to public). The service would be free for nannies to post their bios and only a subscription based service for families to connect with other families or with caregivers (able to view bio but need service to connect). There will be a short bio on the benefits of nanny sharing (reduced cost, increased flexibility for parents, reduced illness, increased socialization with other children vs. sole nanny), as well as Q&A section with best practices.

Target Market(s)

Families, Nannies

Industry/Entity Type

Childcare

Logo Text

Bright Pram Hub

Coding

Coded - Design and coding required

Number of Pages Required

5+ page

Requirements
Must have
• Searchable (need to be able to search for families as well as nannies), responsive, functional, easy to use, add value to families and nannies. Needs to be able to collect payment for subscription.
Nice to have
• Optimized for mobile, SEO optimized

```html
<!DOCTYPE html>
<html lang="en">
<head>
<meta charset="utf-8">
<title>Bright Pram Hub – Nanny Share</title>
<link href="https://fonts.googleapis.com/css2?family=Lato:wght@300;400;700&display=swap" rel="stylesheet">
<style>
:root{
  --red:#f2575a;
  --red-dark:#e54447;
  --ink:#2b2b2b;
  --text:#666;
  --muted:#999;
  --light:#f7f7f7;
  --line:#e6e6e6;
  --white:#fff;
}
*{margin:0;padding:0;box-sizing:border-box}
html,body{width:1200px;height:4176px;overflow:hidden}
body{font-family:'Lato',sans-serif;color:var(--text);background:var(--white);position:relative}
section,header,footer{position:absolute;left:0;width:1200px}

/* header */
.site-header{top:0;height:103px;background:var(--white)}
.brand{position:absolute;left:96px;top:34px;display:flex;align-items:center;gap:12px;font-size:25px;font-weight:400;color:var(--ink);letter-spacing:.5px}
.brand-dot{width:30px;height:30px;border-radius:50%;border:2px solid var(--red)}
.main-nav{position:absolute;right:96px;top:42px;display:flex;gap:46px;font-size:14px;color:var(--ink);text-transform:uppercase}
.main-nav a{color:inherit;text-decoration:none;position:relative}
.main-nav a.active{color:var(--red)}
.main-nav a.active::after{content:"";position:absolute;left:-4px;right:-4px;top:30px;height:2px;background:var(--red)}

/* hero */
.hero{top:103px;height:640px}
.hero-photo{position:absolute;inset:0;background:linear-gradient(120deg,#c9b7a5 0%,#8f7a66 35%,#c7a78c 60%,#6d5a4c 100%)}
.hero-shade{position:absolute;inset:0;background:rgba(0,0,0,.18)}
.hero-title{position:absolute;top:290px;left:0;right:0;text-align:center;font-size:50px;font-weight:300;color:var(--white);letter-spacing:1px}
.hero-sub{position:absolute;top:355px;left:0;right:0;text-align:center;font-size:15px;color:var(--white);font-weight:300}
.hero-actions{position:absolute;top:390px;left:0;right:0;display:flex;justify-content:center;gap:18px}
.btn{display:inline-block;font-size:15px;padding:9px 28px;color:var(--white);text-decoration:none;border-radius:2px}
.btn-solid{background:var(--red)}
.btn-outline{border:1.5px solid var(--white)}
.hero-arrow{position:absolute;right:30px;top:290px}

/* headings */
.section-title{text-align:center;font-size:34px;font-weight:400;color:var(--ink)}

/* services */
.services{top:743px;height:967px}
.services .section-title{margin-top:64px}
.service-card{position:absolute;width:520px;height:310px;display:flex;gap:11px}
.service-photo{position:relative;width:246px;height:310px;flex:none}
.service-photo span{position:absolute;left:10px;bottom:18px;color:var(--white);font-weight:700;font-size:21px;line-height:1.1}
.service-body{width:262px;font-size:13.5px;line-height:1.55;color:var(--text);padding-top:6px}
.service-body .btn{margin-top:34px;font-size:13px;padding:7px 26px}
.ph-child{background:linear-gradient(150deg,#e9d4c4,#b08a6e)}
.ph-senior{background:linear-gradient(150deg,#a9b7bf,#6f7a72)}
.ph-pet{background:linear-gradient(150deg,#8fa66f,#c4b69b)}
.ph-home{background:linear-gradient(150deg,#7e7f86,#c7b3a1)}

/* about */
.about{top:1710px;height:442px}
.about-photo{position:absolute;inset:0;background:linear-gradient(110deg,#8d8883,#c9b6a4 45%,#6c625c)}
.about-shade{position:absolute;inset:0;background:rgba(0,0,0,.25)}
.about-inner{position:absolute;top:120px;left:0;right:0;text-align:center;color:var(--white)}
.about-inner h2{font-size:34px;font-weight:700}
.about-inner p{width:760px;margin:14px auto 0;font-size:18px;line-height:1.35}
.about-inner .btn{margin-top:40px;border:1.5px solid rgba(255,255,255,.7);font-size:15px}

/* benefits */
.benefits{top:2152px;height:548px}
.benefits .section-title{margin-top:74px}
.benefit{position:absolute;top:172px;width:250px;text-align:center}
.benefit svg{display:block;margin:0 auto}
.benefit h3{margin-top:24px;font-size:17px;font-weight:400;color:var(--ink);line-height:1.25}
.benefit p{margin:12px auto 0;width:190px;font-size:13px;line-height:1.5}

/* reviews */
.reviews{top:2700px;height:580px;background:var(--light)}
.reviews .section-title{margin-top:64px}
.quote{position:absolute;top:138px;left:200px;width:800px;text-align:center;font-size:14px;font-weight:300;font-style:italic;line-height:1.6;color:var(--muted)}
.qmark{position:absolute;font-size:80px;color:#ddd;font-family:Georgia,serif;line-height:1}
.avatar{position:absolute;left:530px;top:220px;width:140px;height:140px;border-radius:50%;border:5px solid var(--white);background:linear-gradient(160deg,#b9a08d,#6f5a4f);box-shadow:0 0 0 1px var(--line)}
.reviewer{position:absolute;top:374px;left:0;right:0;text-align:center}
.reviewer h4{font-size:16px;font-weight:700;color:var(--ink)}
.stars{margin-top:8px;color:#f7a776;font-size:20px;letter-spacing:4px}
.reviewer small{display:block;margin-top:8px;font-size:12px;color:var(--muted)}
.dots{position:absolute;top:478px;left:0;right:0;display:flex;justify-content:center;gap:8px}
.dots i{width:10px;height:10px;border-radius:50%;background:var(--red)}
.dots i.off{background:transparent;border:1.5px solid var(--red)}

/* faq */
.faq{top:3280px;height:500px;background:linear-gradient(135deg,#ececec,#f5f5f5 40%,#e4e4e4 70%,#f1f1f1)}
.faq .section-title{margin-top:66px}
.faq-item{position:absolute;left:97px;width:1003px;background:var(--white);padding:26px 68px 0}
.faq-item h5{font-size:17px;font-weight:400;color:var(--ink)}
.faq-item h5 b,.faq-item p b{color:var(--red);font-weight:700}
.faq-item p{margin-top:14px;font-size:12.5px;color:var(--text)}

/* footer */
.site-footer{top:3780px;height:396px;background:var(--red);color:var(--white)}
.news{position:absolute;left:97px;top:76px}
.news h6,.contact h6{font-size:18px;font-weight:400}
.news p{margin-top:12px;font-size:12.5px;opacity:.9}
.news form{margin-top:34px;display:flex;width:465px;height:46px;border:2px solid var(--white)}
.news .field{flex:1;background:var(--white);color:#aaa;font-size:13px;padding:14px 18px}
.news .submit{width:170px;background:var(--red);color:var(--white);font-weight:700;font-size:14px;display:flex;align-items:center;justify-content:center}
.contact{position:absolute;left:852px;top:76px;font-size:13px;line-height:1.6}
.contact ul{list-style:none;margin-top:8px}
.contact li{display:flex;gap:8px;align-items:flex-start}
.contact svg{flex:none;margin-top:4px}
.social{display:flex;gap:8px;margin-top:10px}
.social i{width:28px;height:28px;border-radius:50%;background:rgba(255,255,255,.85)}
.footer-rule{position:absolute;left:97px;right:97px;top:318px;height:1px;background:rgba(255,255,255,.35)}
.copyright{position:absolute;top:346px;left:0;right:0;text-align:center;font-size:11px}
.copyright span{position:absolute;right:105px}
</style>
</head>
<body>

<header class="site-header">
  <div class="brand"><span class="brand-dot"></span>BRIGHTPRAMHUB</div>
  <nav class="main-nav">
    <a class="active" href="#">Home</a><a href="#">About Us</a><a href="#">Our Services</a><a href="#">Testimonials</a><a href="#">FAQ</a><a href="#">Contact Us</a>
  </nav>
</header>

<section class="hero">
  <div class="hero-photo" role="img" aria-label="Photo of a nanny reading a picture book with a young child"></div>
  <div class="hero-shade"></div>
  <h1 class="hero-title">CONNECTS FAMILIES AND CAREGIVERS</h1>
  <p class="hero-sub">Share a trusted nanny with nearby families, split the cost and give your children the company of friends every day.</p>
  <div class="hero-actions"><a class="btn btn-solid" href="#">Find Care</a><a class="btn btn-outline" href="#">Find Nannies</a></div>
  <svg class="hero-arrow" width="16" height="28" viewBox="0 0 16 28"><path d="M2 2l12 12L2 26" fill="none" stroke="#fff" stroke-width="2"/></svg>
</section>

<section class="services">
  <h2 class="section-title">Our Services</h2>
  <div class="service-card" style="left:108px;top:167px">
    <div class="service-photo ph-child" role="img" aria-label="Photo of a mother holding her baby"><span>Child care</span></div>
    <div class="service-body">Find a caring nanny to share with families nearby. Search by age range, schedule, after school care and holiday cover, then read bios, ratings and reviews from other parents before you connect with a provider...<br><a class="btn btn-solid" href="#">Learn more</a></div>
  </div>
  <div class="service-card" style="left:651px;top:167px">
    <div class="service-photo ph-senior" role="img" aria-label="Photo of a smiling senior couple"><span>Adult and<br>senior care</span></div>
    <div class="service-body">Caregivers for older family members who need a kind hand at home. Filter by experience, language, hourly rate and transport, view each profile and book help for the days and hours that suit you...<br><a class="btn btn-solid" href="#">Learn more</a></div>
  </div>
  <div class="service-card" style="left:108px;top:543px">
    <div class="service-photo ph-pet" role="img" aria-label="Photo of two small dogs on a walk"><span>Pet care</span></div>
    <div class="service-body">Walkers and sitters who keep pets happy while the family is at work or away. Compare rates, check reviews and arrange regular visits, walks or overnight stays with a sitter you trust...<br><a class="btn btn-solid" href="#">Learn more</a></div>
  </div>
  <div class="service-card" style="left:651px;top:543px">
    <div class="service-photo ph-home" role="img" aria-label="Photo of a caregiver with an elderly woman at home"><span>Home care</span></div>
    <div class="service-body">Help around the house for busy parents, from light cleaning to meal prep and errands. Browse profiles, check certificates and connect with helpers who fit your home and routine...<br><a class="btn btn-solid" href="#">Learn more</a></div>
  </div>
</section>

<section class="about">
  <div class="about-photo" role="img" aria-label="Photo of a young hand resting on an elderly hand"></div>
  <div class="about-shade"></div>
  <div class="about-inner">
    <h2>About Bright Pram Hub</h2>
    <p>We bring nearby families together so they can share one great nanny, lower the cost of care and give their children friends to grow with, all with simple search and secure subscriptions.</p>
    <a class="btn" href="#">Learn more</a>
  </div>
</section>

<section class="benefits">
  <h2 class="section-title">Our Benefits</h2>
  <div class="benefit" style="left:59px">
    <svg width="106" height="106" viewBox="0 0 106 106"><circle cx="53" cy="53" r="51" fill="none" stroke="#f2575a" stroke-width="2"/><text x="53" y="67" text-anchor="middle" font-family="Lato,sans-serif" font-size="40" font-weight="700" fill="#f2575a">$</text></svg>
    <h3>Reduced Cost</h3>
    <p>Split one nanny's pay between two families and save every month on care.</p>
  </div>
  <div class="benefit" style="left:318px">
    <svg width="106" height="106" viewBox="0 0 106 106"><circle cx="53" cy="53" r="51" fill="none" stroke="#f2575a" stroke-width="2"/><g fill="#f2575a"><circle cx="42" cy="36" r="6"/><circle cx="64" cy="36" r="6"/><circle cx="53" cy="52" r="4"/><rect x="35" y="44" width="14" height="30" rx="3"/><rect x="57" y="44" width="14" height="30" rx="3"/><rect x="49" y="57" width="8" height="17" rx="2"/></g></svg>
    <h3>Increased Flexibility<br>for Parents</h3>
    <p>Share pickups and schedules with a partner family when work runs late.</p>
  </div>
  <div class="benefit" style="left:574px">
    <svg width="106" height="106" viewBox="0 0 106 106"><circle cx="53" cy="53" r="51" fill="none" stroke="#f2575a" stroke-width="2"/><path d="M38 32v18a12 12 0 0 0 24 0V32M50 62v6a10 10 0 0 0 20 0v-6" fill="none" stroke="#f2575a" stroke-width="3"/><circle cx="70" cy="58" r="5" fill="none" stroke="#f2575a" stroke-width="3"/></svg>
    <h3>Reduced Illness</h3>
    <p>Fewer children in care than a daycare room means fewer bugs at home.</p>
  </div>
  <div class="benefit" style="left:855px">
    <svg width="106" height="106" viewBox="0 0 106 106"><circle cx="53" cy="53" r="51" fill="none" stroke="#f2575a" stroke-width="2"/><g fill="#f2575a"><circle cx="48" cy="40" r="8"/><path d="M34 70c0-12 6-18 14-18s14 6 14 18z"/><circle cx="64" cy="58" r="5"/><path d="M56 74c0-7 3-10 8-10s8 3 8 10z"/></g></svg>
    <h3>Increased Socialization with<br>Other Children vs. Sole Nanny</h3>
    <p>Kids learn to share, play and make friends with a buddy every day.</p>
  </div>
</section>

<section class="reviews">
  <h2 class="section-title">Client Reviews</h2>
  <span class="qmark" style="left:168px;top:122px">&ldquo;</span>
  <p class="quote">We found a wonderful nanny and a family two streets away within a week. Our daughters are best friends now, we pay far less than before, and booking cover for school holidays takes only a few clicks on the site. I tell every parent I know about it.</p>
  <span class="qmark" style="left:990px;top:172px">&rdquo;</span>
  <div class="avatar" role="img" aria-label="Portrait of the reviewer"></div>
  <div class="reviewer">
    <h4>Dana Whitfield</h4>
    <div class="stars">★★★★★</div>
    <small>Parent of two, City Name</small>
  </div>
  <div class="dots"><i></i><i class="off"></i><i></i></div>
</section>

<section class="faq">
  <h2 class="section-title">FAQ</h2>
  <div class="faq-item" style="top:130px;height:106px">
    <h5><b>Q:</b> How do two families agree on house rules for a shared nanny?</h5>
    <p><b>A:</b> Meet before you start, write down schedules, meals, naps and pay, and review the plan together after the first month.</p>
  </div>
  <div class="faq-item" style="top:275px;height:109px">
    <h5><b>Q:</b> Can I view nanny profiles before I pay for a subscription?</h5>
    <p><b>A:</b> Yes, every bio, photo and rating is public; you only need a plan when you are ready to message a family or caregiver.</p>
  </div>
</section>

<footer class="site-footer">
  <div class="news">
    <h6>Sign Up for Newsletter</h6>
    <p>Tips on nanny sharing and new families near you, once a month.</p>
    <form><div class="field">Enter your email address</div><div class="submit">SUBSCRIBE NOW !</div></form>
  </div>
  <div class="contact">
    <h6>Contact Us</h6>
    <ul>
      <li><svg width="10" height="14" viewBox="0 0 10 14"><path d="M5 0a5 5 0 0 0-5 5c0 4 5 9 5 9s5-5 5-9a5 5 0 0 0-5-5z" fill="#fff"/><circle cx="5" cy="5" r="2" fill="#f2575a"/></svg><span>Bright Pram Hub, Street Name,<br>City Name, Country Code.</span></li>
      <li><svg width="12" height="12" viewBox="0 0 12 12"><rect width="12" height="12" rx="2" fill="#fff"/><path d="M3 3l2 0 1 2-1 1a5 5 0 0 0 2 2l1-1 2 1v2a7 7 0 0 1-7-7z" fill="#f2575a"/></svg><span>Telephone: 001.555.01472</span></li>
      <li><svg width="12" height="12" viewBox="0 0 12 12"><rect y="2" width="12" height="9" rx="1" fill="#fff"/><path d="M1 3l5 4 5-4" fill="none" stroke="#f2575a"/></svg><span>Email: info@brightpramhub.net</span></li>
    </ul>
    <h6 style="margin-top:18px">Connect With Us</h6>
    <div class="social"><i></i><i></i><i></i><i></i><i></i></div>
  </div>
  <div class="footer-rule"></div>
  <p class="copyright">Copyright © 2016 BRIGHTPRAMHUB. All rights reserved.<span>C16</span></p>
</footer>

</body>
</html>
```